Business Card Design

I am an Event and Wedding Planner in need of an eye catching business card featuring my logo (attached), my contact details, and my company tagline (Making every celebration glow with wonder...) I would like the tagline in font similar the logo's font.
Updates
I have just noticed that my logo has a misspelling so for the final design, I will be uploading a corrected logo as soon as I have it.
My apologies.
Reason: Waiting on a corrected logo...Lantern is misspelled and it should say Weddings not Wedding
The logo has been corrected so now Lantern is spelled correctly and it says Weddings instead of Wedding. Please use Edwardian Script ITC as the font for the tagline so it will match the logo. Thank you for your patience.
Target Market(s)
Engaged couples and people hosting milestone celebrations. 25-50 years old, predominately female
Industry/Entity Type
Business
Contact Information for Business Card
Rosalind Merrow, Event Manager / Owner, Mobile: 0491 868 254, Email: rosalind@velvetlanternco.com.au, www.velvetlanternco.com.au, Making every celebration glow with wonder...

```html
<!DOCTYPE html>
<html lang="en">
<head>
<meta charset="utf-8">
<title>Velvet Lantern – Business Card</title>
<link href="https://fonts.googleapis.com/css2?family=Exo+2:wght@400;500&family=Pinyon+Script&display=swap" rel="stylesheet">
<style>
  :root {
    --page: #3a3a3c;
    --card-light: #ffffff;
    --card-shade: #e4e4e4;
    --ink: #1a1a1a;
    --ink-soft: #333333;
    --band: #000000;
    --icon-mute: #8c8c8c;
    --rule-soft: #6e6e6e;
  }
  * { margin: 0; padding: 0; box-sizing: border-box; }
  html, body {
    width: 1200px; height: 816px; overflow: hidden;
    background: var(--page);
    font-family: "Exo 2", sans-serif;
    color: var(--ink);
  }
  .card {
    position: absolute; left: 40px; top: 58px;
    width: 1120px; height: 700px;
    border-radius: 44px; overflow: hidden;
    background: radial-gradient(ellipse at 32% 55%, var(--card-light) 0%, var(--card-light) 35%, var(--card-shade) 100%);
  }
  .brand-panel {
    position: absolute; right: 0; top: 0;
    width: 460px; height: 700px;
    background: var(--card-light);
  }
  .band { position: absolute; left: 0; top: 0; width: 1120px; height: 700px; }
  .vertical {
    position: absolute; top: 350px;
    transform: translate(-50%, -50%) rotate(90deg);
    white-space: nowrap;
  }
  .brand-name {
    left: 975px;
    font-size: 62px; font-weight: 400; letter-spacing: 2px;
    color: var(--ink);
  }
  .brand-rule {
    position: absolute; left: 892px; top: 110px;
    width: 2px; height: 480px;
    background: var(--rule-soft);
  }
  .tagline {
    left: 850px;
    font-family: "Pinyon Script", cursive;
    font-size: 32px;
    color: var(--ink);
  }
  .rule { position: absolute; height: 7px; background: var(--ink); }
  .rule--top { left: 250px; top: 196px; width: 330px; }
  .rule--bottom { left: 60px; top: 330px; width: 400px; }
  .identity {
    position: absolute; left: 70px; top: 222px;
    display: flex; align-items: center; gap: 22px;
  }
  .person-name {
    font-size: 28px; font-weight: 500; letter-spacing: 2px; text-transform: uppercase; line-height: 1.15;
  }
  .person-role { font-size: 23px; letter-spacing: 2px; color: var(--ink-soft); }
  .contact {
    position: absolute; left: 90px;
    display: flex; align-items: center; gap: 24px;
  }
  .contact--phone { top: 370px; }
  .contact--web { top: 468px; }
  .contact--place { top: 566px; }
  .contact-lines { font-size: 22px; letter-spacing: 1px; line-height: 1.35; color: var(--ink-soft); }
  .icon { width: 60px; height: 60px; flex: none; }
</style>
</head>
<body>
  <main class="card">
    <div class="brand-panel"></div>
    <svg class="band" viewBox="0 0 1120 700" aria-hidden="true">
      <polygon fill="var(--band)" points="640,0 730,0 740,60 660,350 740,640 730,700 640,700 650,650 560,350 650,50"/>
      <polygon fill="#ffffff" points="730,0 760,0 690,350 760,700 730,700 740,640 660,350 740,60"/>
    </svg>

    <div class="vertical brand-name">Velvet Lantern</div>
    <div class="brand-rule"></div>
    <div class="vertical tagline">Making every celebration glow with wonder...</div>

    <div class="rule rule--top"></div>
    <div class="identity">
      <svg class="icon" viewBox="0 0 60 60" aria-hidden="true">
        <circle cx="30" cy="30" r="29" fill="var(--icon-mute)"/>
        <circle cx="30" cy="23" r="9" fill="#fff"/>
        <path d="M14 46c2-10 9-14 16-14s14 4 16 14z" fill="#fff"/>
      </svg>
      <div>
        <div class="person-name">Rosalind Merrow</div>
        <div class="person-role">Managing Director</div>
      </div>
    </div>
    <div class="rule rule--bottom"></div>

    <div class="contact contact--phone">
      <svg class="icon" viewBox="0 0 60 60" aria-hidden="true">
        <circle cx="30" cy="30" r="29" fill="var(--ink)"/>
        <rect x="21" y="13" width="18" height="34" rx="3" fill="#fff"/>
        <rect x="24" y="17" width="12" height="23" fill="var(--ink)"/>
        <circle cx="30" cy="43.5" r="1.8" fill="var(--ink)"/>
      </svg>
      <div class="contact-lines">0491 868 254<br>03 9418 2270</div>
    </div>

    <div class="contact contact--web">
      <svg class="icon" viewBox="0 0 60 60" aria-hidden="true">
        <circle cx="30" cy="30" r="29" fill="var(--ink)"/>
        <rect x="14" y="17" width="32" height="21" rx="2" fill="#fff"/>
        <rect x="17" y="20" width="26" height="15" fill="var(--ink)"/>
        <rect x="26" y="38" width="8" height="5" fill="#fff"/>
        <rect x="21" y="43" width="18" height="3" fill="#fff"/>
      </svg>
      <div class="contact-lines">rosalind@velvetlanternco.com.au<br>www.velvetlanternco.com.au</div>
    </div>

    <div class="contact contact--place">
      <svg class="icon" viewBox="0 0 60 60" aria-hidden="true">
        <circle cx="30" cy="30" r="29" fill="var(--ink)"/>
        <path d="M30 12c-7 0-12 5-12 12 0 9 12 24 12 24s12-15 12-24c0-7-5-12-12-12z" fill="#fff"/>
        <circle cx="30" cy="24" r="4.5" fill="var(--ink)"/>
      </svg>
      <div class="contact-lines">Suite 4, 12 Harbour Walk<br>Geelong VIC</div>
    </div>
  </main>
</body>
</html>
```